Vitamin B12 Liquid Drops Label

hi, i need a label designed for my vitamin b12 drops that i am going to be selling on shopzello. the label needs to quickly capture the attention of a buyer as he or she is scrolling through the thumbnail search results on shopzello.com my brand is called nralo. i already have an example brand logo i will be using, however, i need help designing the rest of the label. attached are some examples of labels i like for other supplements.some of these examples are pink. i do not want pink. please go for a blue/green color scheme. THE DESIGN MUST BE BOLD

Target Market(s)

adults ages 30 - 64

Font styles to use
Sans Serif

Colors
0455a3
cedeed
3176b5
85acd3
cfdeed
9bcb3b
abd037
cadf82
00a990

Requirements
Must have
• - bold design
• - somewhat gender-neutral color scheme because this will be used equally by men and women
• - B12 MUST be very prominent and visible on the label
Should not have
• - it should not be "crunchy" looking

```html
<!DOCTYPE html>
<html lang="en">
<head>
<meta charset="utf-8">
<title>nralo Vitamin B12 Drops – Box and Label</title>
<link rel="stylesheet" href="https://fonts.googleapis.com/css2?family=Baloo+2:wght@600;700;800&display=swap">
<style>
  :root {
    --stage: #2b2b2b;
    --brand-blue: #0455a3;
    --mid-blue: #3176b5;
    --soft-blue: #85acd3;
    --pale-blue: #cedeed;
    --brand-green: #9bcb3b;
    --lime: #abd037;
    --pale-lime: #cadf82;
    --teal: #00a990;
  }
  html, body {
    margin: 0;
    padding: 0;
    width: 1200px;
    height: 800px;
    overflow: hidden;
    background: var(--stage);
  }
  .canvas {
    position: relative;
    width: 1200px;
    height: 800px;
    font-family: "Baloo 2", Arial, sans-serif;
  }
  .box-front {
    position: absolute;
    left: 210px;
    top: 90px;
    width: 300px;
    height: 620px;
  }
  .bottle-label {
    position: absolute;
    left: 620px;
    top: 160px;
    width: 380px;
    height: 480px;
  }
  .brand-name { font-weight: 800; letter-spacing: 1px; }
  .product-name { font-weight: 800; letter-spacing: 2px; }
  .hero-b12 { font-weight: 800; }
  .spec { font-weight: 700; }
</style>
</head>
<body>
<main class="canvas">

  <!-- Carton front panel -->
  <svg class="box-front" viewBox="0 0 300 620" aria-label="nralo Vitamin B12 carton front">
    <rect class="panel" width="300" height="620" fill="var(--brand-green)"/>
    <rect class="top-band" width="300" height="40" fill="var(--brand-blue)"/>
    <polygon class="lower-stripe" points="0,470 70,440 300,570 300,620 255,620 0,500" fill="var(--teal)"/>
    <polygon class="title-band" points="0,345 300,215 300,325 0,455" fill="var(--brand-blue)"/>

    <g class="logo-lockup" transform="translate(30 285) rotate(-23.4)">
      <circle cx="14" cy="-20" r="14" fill="var(--brand-blue)"/>
      <text class="brand-name" x="38" y="0" font-size="64" fill="var(--brand-blue)">NRALO</text>
    </g>
    <text class="product-name" transform="translate(22 425) rotate(-23.4)" font-size="40" fill="var(--pale-lime)">VITAMIN B12</text>
  </svg>

  <!-- Dropper bottle label -->
  <svg class="bottle-label" viewBox="0 0 380 480" aria-label="nralo Vitamin B12 bottle label">
    <rect class="label-base" width="380" height="480" fill="var(--brand-blue)"/>
    <polygon class="hero-panel" points="0,0 340,0 282,245 0,245" fill="var(--brand-green)"/>
    <text class="hero-b12" x="14" y="200" font-size="150" fill="var(--brand-blue)">B12</text>

    <text class="spec dose" x="18" y="300" font-size="30" fill="var(--pale-lime)">5000 MCG*</text>
    <text class="spec form" x="18" y="340" font-size="30" letter-spacing="6" fill="var(--pale-lime)">METHYL</text>
    <text class="spec form-sub" x="18" y="367" font-size="17" letter-spacing="6" fill="var(--pale-blue)">COBAMALIN</text>

    <text class="spec origin" x="18" y="425" font-size="22" fill="var(--pale-lime)">MADE IN</text>
    <text class="spec origin" x="18" y="455" font-size="22" letter-spacing="14" fill="var(--pale-lime)">USA</text>

    <g class="logo-lockup">
      <circle cx="200" cy="424" r="14" fill="var(--brand-green)"/>
      <text class="brand-name" x="222" y="438" font-size="44" fill="var(--brand-green)">NRALO</text>
    </g>
  </svg>

</main>
</body>
</html>
```